Business Card: RW Office Partners - Your organised problem solver

Business Name: RW Office Partners
Website: www.rwofficepartners.com.au
Email: marisol@rwofficepartners.com.au
Mobile: 61 482 907 236
Facebook: @rwofficepartners
Instrgram: @rwofficepartners

Brading Colours:
HEX
#986474
#ddccd3
#7a8498
#c9d8e4
#000000
#ffffff

Tag Line: Your organised problem solver

Link to DRAFT website:
https://deskhelpcollective.wixsite.com/rw-office-partners

About Page from the website:
My name is Marisol Wrenfield, and I would love to assist you to become more productive in your day to day and achieve your business and personal goals.
My mission is to give you time, time to work on the important tasks of your business or to be able to spend more time with your family. I will take on the tasks you don’t have time for, don’t know well or simply don’t like to do.
I have an extensive background in Administration, Tender Coordination, Document Control, WHS and Quality Management working primarily in the Construction, Mining and Corporate World.
I am passionate about being organised, having order and making things in your life (and mine) easier! I love to watch something unfold and grow into something amazing! I am known for being the go-to problem solver, the organiser of all things, producing high standards of work even under pressure. I’m also a confident communicator, and I understand that you’re busy running your business.

Target Market(s)

Small to Medium Business who require assistance in their business by a virtual assistant.

Industry/Entity Type

Virtual Assistant

Contact Information for Business Card

Mobile: 61 482 907 236

Font styles to use
Sans Serif

Colors
ffffff

Requirements
Must have
• Branding Colours as outlined.
Contact Details as outlined.
Logo as provided.
Proper contact details - mobile, facebook, instragm, website.
Simple, Elegant, very clean looking.
Should not have
• Note cute with pictures.
Not too girly as still want to market to construction companies.

```html
<!DOCTYPE html>
<html lang="en">
<head>
<meta charset="utf-8">
<title>RW Office Partners – Business Card</title>
<link rel="stylesheet" href="https://fonts.googleapis.com/css2?family=Montserrat:wght@500&family=Roboto:wght@400;700&family=Kalam:wght@400&display=swap">
<style>
  :root {
    --mauve: #986474;
    --mauve-band: #855a6b;
    --blush: #ddccd3;
    --slate: #7a8498;
    --mist: #c9d8e4;
    --ink: #000000;
    --card: #1f1e21;
    --white: #ffffff;
    --page: #3a3a3c;
  }
  * { margin: 0; padding: 0; box-sizing: border-box; }
  html, body { width: 799px; height: 1200px; overflow: hidden; }
  body {
    background: var(--page);
    font-family: "Roboto", Arial, sans-serif;
    position: relative;
  }
  .card {
    position: absolute;
    left: 50px;
    width: 700px;
    height: 400px;
    background: var(--card);
    border-radius: 4px;
    overflow: hidden;
    box-shadow: 0 12px 30px rgba(0,0,0,.45);
  }
  .card--front { top: 130px; }
  .card--back { top: 670px; }

  /* front */
  .front-name {
    position: absolute;
    left: 0; right: 0; top: 140px;
    text-align: center;
    font-family: "Montserrat", Arial, sans-serif;
    font-weight: 500;
    font-size: 50px;
    letter-spacing: 1px;
    color: #4a494d;
  }
  .social-row {
    position: absolute;
    left: 0; right: 0; top: 292px;
    display: flex;
    justify-content: center;
    gap: 28px;
    color: var(--white);
    font-size: 20px;
  }
  .social-item { display: flex; align-items: center; gap: 9px; }
  .social-mark {
    width: 15px; height: 15px;
    border-radius: 3px;
    background: var(--mauve);
  }

  /* back */
  .back-name {
    position: absolute;
    left: 34px; top: 24px;
    font-family: "Montserrat", Arial, sans-serif;
    font-weight: 500;
    font-size: 36px;
    color: var(--slate);
  }
  .tagline {
    position: absolute;
    left: 36px; top: 72px;
    font-family: "Kalam", cursive;
    font-size: 22px;
    color: var(--white);
  }
  .contact-list {
    position: absolute;
    left: 36px; top: 114px;
    list-style: none;
    color: var(--white);
    font-size: 17px;
    line-height: 22px;
  }
  .contact-list li { display: flex; align-items: center; gap: 10px; }
  .contact-icon { width: 13px; height: 13px; flex: none; }
  .contact-square {
    width: 12px; height: 12px; flex: none;
    border-radius: 2px;
    background: var(--mauve);
  }
  .wave { position: absolute; left: 0; top: 0; }
  .person {
    position: absolute;
    right: 40px; top: 342px;
    text-align: right;
    color: var(--white);
  }
  .person-name { font-weight: 700; font-size: 25px; line-height: 28px; }
  .person-role { font-size: 17px; line-height: 20px; margin-top: 2px; }
</style>
</head>
<body>

<section class="card card--front">
  <div class="front-name">RW Office Partners</div>
  <div class="social-row">
    <span class="social-item"><span class="social-mark"></span>@rwofficepartners</span>
    <span class="social-item"><span class="social-mark"></span>@rwofficepartners</span>
  </div>
</section>

<section class="card card--back">
  <svg class="wave" width="700" height="400" viewBox="0 0 700 400">
    <path d="M0,282 C130,340 260,350 400,345 C520,340 620,318 700,300 L700,400 L0,400 Z" fill="var(--mauve-band)"/>
    <path d="M0,266 C140,325 280,333 420,328 C560,322 640,295 700,280" fill="none" stroke="var(--ink)" stroke-width="9"/>
    <path d="M0,250 C150,310 300,318 430,313 C560,308 640,275 700,258" fill="none" stroke="var(--slate)" stroke-width="9"/>
  </svg>

  <div class="back-name">RW Office Partners</div>
  <div class="tagline">Your organised problem solver</div>

  <ul class="contact-list">
    <li>
      <svg class="contact-icon" viewBox="0 0 14 14"><path d="M2 1h3l1 3-2 1.5c.8 1.8 2 3 3.5 3.5L9 7l3 1v3c0 1-1 2-2 2C5 12.5 1.5 9 1 4c0-1 .5-3 1-3z" fill="var(--mauve)"/></svg>
      61 482 907 236
    </li>
    <li>
      <svg class="contact-icon" viewBox="0 0 14 14"><rect x="1" y="3" width="12" height="8" fill="var(--mauve)"/><path d="M1 3l6 5 6-5" fill="none" stroke="var(--card)" stroke-width="1.2"/></svg>
      marisol@rwofficepartners.com.au
    </li>
    <li>
      <svg class="contact-icon" viewBox="0 0 14 14"><circle cx="7" cy="7" r="5.5" fill="none" stroke="var(--mauve)" stroke-width="1.5"/><path d="M1.5 7h11M7 1.5c-2.5 3-2.5 8 0 11M7 1.5c2.5 3 2.5 8 0 11" fill="none" stroke="var(--mauve)" stroke-width="1.2"/></svg>
      www.rwofficepartners.com.au
    </li>
    <li><span class="contact-square"></span>@rwofficepartners</li>
    <li><span class="contact-square"></span>@rwofficepartners</li>
  </ul>

  <div class="person">
    <div class="person-name">Marisol Wrenfield</div>
    <div class="person-role">Virtual Assistant</div>
  </div>
</section>

</body>
</html>
```